Business Card Design - Photographer

I am a landscape photographer and I require a business card design. 

I require two designs:
1)  a double sided business card
 and
b)  a single sided business card 

The single sided design can either be the same as the double sided (with just one side having all the information)....or it can be an entire new design. Its up to you.

My corporate colours are (CMYK):

Blue   69, 32, 0, 0
Grey  72,  64,  47,  31
Green  32,  2,  91,  0
Yellow   0, 19, 92, 0
Orange  0, 39, 75, 0

Colour space in final file should be in CMYK.

The details that need to be included on the card:

- Use the provided Logo
- Name: Wiktor Baranowski
- Email:   sales@vistalumeworks.com.au
- Website:    vistalumeworks.com.au
- Twitter:    twitter.com/vistalumeworks
- Facebook:   facebook.com/vistalumeworks
- Mobile  0417 539 662

Please use the attached template to design the logo to the specified size, including the marked bleed lines. I have also attached my logo in PNG (transparent background) and ai format for you to use.

The final file should be:
- Photoshop version with layers so I can edit the name/text etc. All non vector files should be high resolution at 1039 x 697 pixels at 300 dpi.

I also require a file as:
- Vector based PDF

Anyway questions please contact me.

Thank you

Industry/Entity Type

Landscape

Logo styles of interest
Pictorial/Combination Logo
Abstract Logo
Wordmark Logo
Lettermark Logo
Requirements
Must have
• The details that need to be included on the card:

- Use the provided Logo
- Name: Wiktor Baranowski
- Email: sales@vistalumeworks.com.au
- Website: vistalumeworks.com.au
- Twitter: twitter.com/vistalumeworks
- Facebook: facebook.com/vistalumeworks
- Mobile 0417 539 662

```html
<!DOCTYPE html>
<html lang="en">
<head>
<meta charset="utf-8">
<title>Vistalume Works – Business Cards</title>
<link rel="stylesheet" href="https://fonts.googleapis.com/css2?family=Cinzel:wght@600&family=Tinos:wght@400;700&family=PT+Sans&display=swap">
<style>
  :root {
    --stage: #e9e6e1;
    --card-white: #ffffff;
    --brand-blue: #3e8ecf;
    --brand-grey: #474b5c;
    --text-light: #ffffff;
    --rule-light: rgba(255,255,255,0.75);
  }
  * { margin: 0; padding: 0; box-sizing: border-box; }
  html, body {
    width: 1200px; height: 1022px; overflow: hidden;
    background: var(--stage);
  }
  .canvas { position: relative; width: 1200px; height: 1022px; }

  .card {
    position: absolute; width: 738px; height: 422px; overflow: hidden;
    box-shadow: 0 2px 6px rgba(0,0,0,0.18);
  }
  .card--front { left: 73px; top: 59px; background: var(--card-white); }
  .card--back  { left: 379px; top: 532px; background: var(--brand-blue); }

  .brand-dot {
    position: absolute; width: 124px; height: 124px; border-radius: 50%;
    background: var(--brand-grey);
  }
  .card--front .brand-dot { left: 298px; top: 28px; }
  .card--back .brand-dot { left: 306px; top: 78px; }

  .brand-name {
    position: absolute; left: 0; width: 100%; text-align: center;
    font-family: "Cinzel", serif; font-weight: 600;
    color: var(--brand-grey); letter-spacing: 0.5px; white-space: nowrap;
  }
  .card--front .brand-name { top: 161px; font-size: 33px; line-height: 36px; }
  .card--back .brand-name { top: 227px; font-size: 36px; line-height: 40px; }

  .brand-rule {
    position: absolute; height: 2px; background: var(--brand-grey);
  }
  .card--front .brand-rule { left: 180px; top: 199px; width: 378px; }
  .card--back .brand-rule { left: 184px; top: 268px; width: 371px; }

  .tagline {
    position: absolute; left: 0; width: 100%; text-align: center;
    font-family: "Cinzel", serif; font-weight: 600;
    color: var(--brand-grey); letter-spacing: 2.5px; white-space: nowrap;
  }
  .card--front .tagline { top: 206px; font-size: 13px; line-height: 18px; }
  .card--back .tagline { top: 276px; font-size: 14px; line-height: 20px; }

  .front-rule {
    position: absolute; left: 0; top: 247px; width: 100%; height: 4px;
    background: var(--brand-grey);
  }
  .contact-band {
    position: absolute; left: 0; top: 258px; width: 100%; height: 164px;
    background: var(--brand-blue);
    font-family: "Tinos", serif; color: var(--text-light); font-size: 18.5px;
  }
  .holder {
    position: absolute; right: 440px; top: 18px; text-align: right;
    font-weight: 700; font-size: 20px; line-height: 27px; white-space: nowrap;
  }
  .address {
    position: absolute; right: 440px; top: 54px; text-align: right;
    line-height: 27px; font-style: normal;
  }
  .band-divider {
    position: absolute; left: 330px; top: 14px; width: 1px; height: 134px;
    background: var(--rule-light);
  }
  .contact-list { position: absolute; left: 357px; top: 14px; list-style: none; }
  .contact-list li {
    display: flex; align-items: center; height: 27px; line-height: 27px;
  }
  .contact-icon { width: 11px; height: 11px; margin-right: 6px; flex: none; }

  .back-url {
    position: absolute; left: 0; top: 340px; width: 100%; text-align: center;
    font-family: "PT Sans", sans-serif; font-size: 18px; letter-spacing: 3px;
    color: var(--text-light);
  }
</style>
</head>
<body>
<main class="canvas">

  <section class="card card--front" aria-label="Business card front">
    <div class="brand-dot"></div>
    <div class="brand-name">VISTALUME WORKS</div>
    <div class="brand-rule"></div>
    <div class="tagline">FINE ART PHOTOGRAPHY</div>
    <div class="front-rule"></div>

    <div class="contact-band">
      <div class="holder">Wiktor Baranowski</div>
      <address class="address">00, Complex Name<br>State Name, City 0020</address>
      <div class="band-divider"></div>
      <ul class="contact-list">
        <li>
          <svg class="contact-icon" viewBox="0 0 11 11" aria-hidden="true">
            <rect x="2.5" y="0.5" width="6" height="10" rx="1.2" fill="none" stroke="#fff" stroke-width="1.2"/>
            <circle cx="5.5" cy="8.5" r="0.8" fill="#fff"/>
          </svg>0417 539 662
        </li>
        <li>
          <svg class="contact-icon" viewBox="0 0 11 11" aria-hidden="true"><rect x="0.5" y="0.5" width="10" height="10" fill="#fff"/></svg>vistalumeworks
        </li>
        <li>
          <svg class="contact-icon" viewBox="0 0 11 11" aria-hidden="true"><rect x="0.5" y="0.5" width="10" height="10" fill="#fff"/></svg>vistalumeworks
        </li>
        <li>
          <svg class="contact-icon" viewBox="0 0 11 11" aria-hidden="true">
            <rect x="0.5" y="2" width="10" height="7" fill="#fff"/>
            <polyline points="0.5,2 5.5,6 10.5,2" fill="none" stroke="#3e8ecf" stroke-width="1"/>
          </svg>sales@vistalumeworks.com.au
        </li>
        <li>
          <svg class="contact-icon" viewBox="0 0 11 11" aria-hidden="true"><circle cx="5.5" cy="5.5" r="5" fill="#fff"/></svg>www.vistalumeworks.com.au
        </li>
      </ul>
    </div>
  </section>

  <section class="card card--back" aria-label="Business card back">
    <div class="brand-dot"></div>
    <div class="brand-name">VISTALUME WORKS</div>
    <div class="brand-rule"></div>
    <div class="tagline">FINE ART PHOTOGRAPHY</div>
    <div class="back-url">www.vistalumeworks.com.au</div>
  </section>

</main>
</body>
</html>
```